Veranix - Solution provider in business consulting

Veranix is a swiss based company providing solutions for developing markets. The business covers various fields of business consulting, such as supply chain, product costs, quality management and manufacturing management. The Business operates in a efficient, straight and solution oriented manner.
The final design should communicate these characteristics. Asian people as well as as western people shall identify the qualities of the company at first sight.
The customer needs business cards with a simple view but an recognizable design, printed in high quality. Engraved elements such as the globe or simple words are possible.
Available colors are: (RAL)
102/102/102
51/102/102
153/204/153
255/102/51
Font: Calibri

```html
<!DOCTYPE html>
<html lang="en">
<head>
<meta charset="utf-8">
<title>Veranix business card</title>
<link href="https://fonts.googleapis.com/css2?family=Carlito:wght@400;700&display=swap" rel="stylesheet">
<style>
  :root {
    --page-bg: #e9e7e3;
    --card-light: #7a7a7a;
    --card-mid: #666666;
    --card-dark: #4a4a4a;
    --ink: #f2f2f2;
    --ink-soft: #d6d6d6;
    --rule: #cfcfcf;
    --globe-light: rgba(255,255,255,0.10);
    --globe-dark: rgba(0,0,0,0.10);
  }
  html, body {
    margin: 0;
    width: 1200px;
    height: 1022px;
    overflow: hidden;
    background: var(--page-bg);
    font-family: "Carlito", "Calibri", sans-serif;
  }
  .card {
    position: absolute;
    left: 100px;
    top: 231px;
    width: 1000px;
    height: 560px;
    border-radius: 22px;
    overflow: hidden;
    background: linear-gradient(135deg, var(--card-light) 0%, var(--card-mid) 45%, var(--card-dark) 100%);
    color: var(--ink);
  }
  .globe-decoration {
    position: absolute;
    right: -120px;
    top: -110px;
    width: 620px;
    height: 620px;
    border-radius: 50%;
    background: radial-gradient(circle at 40% 40%, var(--globe-light) 0%, var(--globe-dark) 100%);
  }
  .brand {
    position: absolute;
    left: 70px;
    top: 150px;
    display: flex;
    align-items: center;
    gap: 18px;
  }
  .brand-dot {
    width: 70px;
    height: 70px;
    border-radius: 50%;
    background: var(--ink);
  }
  .brand-name {
    font-size: 104px;
    font-weight: 400;
    line-height: 1;
    letter-spacing: 1px;
    color: var(--ink);
  }
  .divider {
    position: absolute;
    left: 70px;
    right: 150px;
    top: 345px;
    height: 1.5px;
    background: var(--rule);
  }
  .person {
    position: absolute;
    right: 70px;
    top: 70px;
    text-align: right;
  }
  .person-name {
    font-size: 40px;
    font-weight: 700;
    margin: 0;
  }
  .person-role {
    font-size: 22px;
    margin: 2px 0 0;
    color: var(--ink-soft);
  }
  .address {
    position: absolute;
    right: 70px;
    top: 180px;
    text-align: right;
    font-size: 24px;
    line-height: 1.45;
    color: var(--ink-soft);
  }
  .contact {
    position: absolute;
    left: 70px;
    top: 370px;
    margin: 0;
    padding: 0;
    list-style: none;
    font-size: 26px;
    line-height: 1.45;
  }
  .contact li {
    display: flex;
    align-items: center;
    gap: 14px;
  }
  .contact svg {
    width: 20px;
    height: 20px;
    fill: none;
    stroke: var(--ink);
    stroke-width: 1.6;
  }
</style>
</head>
<body>
  <div class="card">
    <div class="globe-decoration" role="img" aria-label="Faint engraved world globe decoration"></div>

    <div class="brand">
      <span class="brand-name">Veranix</span>
      <span class="brand-dot"></span>
    </div>

    <div class="person">
      <p class="person-name">Marten Kolb</p>
      <p class="person-role">CEO</p>
    </div>

    <div class="address">
      Veranix GmbH Lindenweg<br>
      14 9246 Niederau Switzerland
    </div>

    <div class="divider"></div>

    <ul class="contact">
      <li>
        <svg viewBox="0 0 20 20" aria-hidden="true"><rect x="5" y="2" width="10" height="16" rx="2"/><line x1="8" y1="15" x2="12" y2="15"/></svg>
        +41 78 302 5817
      </li>
      <li>
        <svg viewBox="0 0 20 20" aria-hidden="true"><path d="M4 3 L8 3 L9 7 L7 9 Q9 12 11 13 L13 11 L17 12 L17 16 Q10 17 6 13 Q3 9 4 3 Z"/></svg>
        +41 71 640 3962
      </li>
      <li>
        <svg viewBox="0 0 20 20" aria-hidden="true"><rect x="2" y="4" width="16" height="12" rx="1"/><polyline points="2,5 10,11 18,5"/></svg>
        marten.kolb@veranix.ch
      </li>
      <li>
        <svg viewBox="0 0 20 20" aria-hidden="true"><circle cx="10" cy="10" r="8"/><ellipse cx="10" cy="10" rx="3.5" ry="8"/><line x1="2" y1="10" x2="18" y2="10"/></svg>
        www.veranix.ch
      </li>
    </ul>
  </div>
</body>
</html>
```